I have an animal hospital. I want a poster to hang in each exam room to show a picture of a normal sized heart and then an enlarged heart of a dog that was fed a grain-free diet. I want to warn people not to feed grain-free diets. Maybe at the top of the poster, "Do you feed grain-free?" and then the x-ray comparison, then the warnings of Canine Dilated Cardiomyopathy.

```html
<!DOCTYPE html>
<html lang="en">
<head>
<meta charset="utf-8">
<title>Do You Feed Grain-Free? – Heart Health Poster</title>
<link rel="stylesheet" href="https://fonts.googleapis.com/css2?family=Oswald:wght@600;700&family=Encode+Sans+Condensed:wght@300;400;700;800&display=swap">
<style>
  :root {
    --navy: #36388a;
    --band: #3a3a88;
    --red: #b22025;
    --coral: #f26666;
    --green: #3a9a35;
    --ink: #1a1a1a;
    --paper: #ffffff;
  }
  * { margin: 0; padding: 0; box-sizing: border-box; }
  html, body { width: 810px; height: 1200px; overflow: hidden; background: var(--paper); }
  .poster { position: relative; width: 810px; height: 1200px; overflow: hidden; background: var(--paper); font-family: "Encode Sans Condensed", sans-serif; color: var(--ink); }

  .headline {
    position: absolute; top: 38px; left: 0; width: 100%;
    text-align: center; font-family: "Oswald", sans-serif; font-weight: 700;
    font-size: 52px; line-height: 1; color: var(--navy); letter-spacing: 0.3px;
  }
  .headline em { color: var(--red); font-style: italic; }

  .xray { position: absolute; top: 128px; width: 387px; height: 386px;
    background: radial-gradient(ellipse at 50% 50%, #d9d9d9 0%, #9a9a9a 35%, #4a4a4a 65%, #0a0a0a 100%); }
  .xray--normal { left: 12px; }
  .xray--enlarged { left: 410px;
    background: radial-gradient(ellipse 60% 55% at 50% 58%, #e6e6e6 0%, #bdbdbd 45%, #5a5a5a 75%, #050505 100%); }
  .xray svg { position: absolute; }
  .xray--normal svg { left: 149px; top: 152px; }
  .xray--enlarged svg { left: 150px; top: 187px; }

  .caption { position: absolute; top: 530px; width: 387px; text-align: center;
    font-size: 23px; font-weight: 400; line-height: 1.2; }
  .caption--normal { left: 12px; }
  .caption--enlarged { left: 410px; }
  .caption em { font-weight: 700; }

  .warning-band { position: absolute; top: 577px; left: 0; width: 810px; height: 198px;
    background: var(--band); color: var(--paper); text-align: center; }
  .warning-band h2 { margin-top: 26px; font-size: 43px; font-weight: 800; letter-spacing: 0.3px; line-height: 1; }
  .warning-band p { margin-top: 16px; font-size: 31px; font-weight: 300; line-height: 44px; }
  .warning-band p em { color: var(--coral); font-weight: 700; }

  .signs-label { position: absolute; left: 63px; top: 818px; font-size: 23px; font-weight: 400; }
  .dog-photo { position: absolute; left: 62px; top: 812px; width: 513px; height: 212px;
    background: radial-gradient(ellipse 50% 45% at 55% 55%, #a85a2a 0%, #c27a45 45%, rgba(230,190,160,0.4) 75%, rgba(255,255,255,0) 100%); }
  .signs-list { position: absolute; right: 48px; top: 826px; list-style: none; text-align: right;
    font-size: 24px; font-weight: 300; line-height: 34.7px; }

  .call-to-action { position: absolute; left: 37px; top: 1062px; font-size: 44px; font-weight: 300;
    color: var(--navy); line-height: 57px; letter-spacing: -0.5px; white-space: nowrap;
    transform: scaleX(0.86); transform-origin: left top; }
  .call-to-action strong { font-weight: 800; }
  .call-to-action .heart-word { color: var(--red); font-weight: 800; }
  .call-to-action .checked-word { color: var(--green); font-weight: 800; }
  .heart-doodle { position: absolute; left: 660px; top: 1010px; }
</style>
</head>
<body>
<main class="poster">
  <h1 class="headline">DO YOU FEED <em>GRAIN-FREE</em>?</h1>

  <div class="xray xray--normal" role="img" aria-label="Chest x-ray of a dog with a normal sized heart">
    <svg width="92" height="80" viewBox="0 0 92 80" aria-hidden="true">
      <path d="M46 74 L10 38 C-2 25 6 5 24 5 C34 5 41 11 46 18 C51 11 58 5 68 5 C86 5 94 25 82 38 Z"
            fill="none" stroke="var(--green)" stroke-width="5" stroke-linejoin="round"/>
    </svg>
  </div>
  <div class="xray xray--enlarged" role="img" aria-label="Chest x-ray of a dog on a grain-free diet showing an enlarged heart">
    <svg width="92" height="92" viewBox="0 0 92 92" aria-hidden="true">
      <circle cx="46" cy="46" r="41" fill="none" stroke="var(--red)" stroke-width="6"/>
      <line x1="17" y1="17" x2="75" y2="75" stroke="var(--red)" stroke-width="6"/>
      <g fill="var(--red)">
        <line x1="38" y1="70" x2="52" y2="26" stroke="var(--red)" stroke-width="3"/>
        <ellipse cx="53" cy="24" rx="4" ry="8" transform="rotate(20 53 24)"/>
        <ellipse cx="45" cy="36" rx="4" ry="7" transform="rotate(-30 45 36)"/>
        <ellipse cx="56" cy="40" rx="4" ry="7" transform="rotate(60 56 40)"/>
        <ellipse cx="41" cy="48" rx="4" ry="7" transform="rotate(-30 41 48)"/>
        <ellipse cx="52" cy="53" rx="4" ry="7" transform="rotate(60 52 53)"/>
      </g>
    </svg>
  </div>
  <p class="caption caption--normal">Normal heart</p>
  <p class="caption caption--enlarged">Heart of a dog on a <em>grain-free diet</em></p>

  <section class="warning-band">
    <h2>CANINE DILATED CARDIOMYOPATHY</h2>
    <p>is a <em>serious</em> and <em>often fatal</em> condition<br>in dogs caused by a grain-free diet</p>
  </section>

  <div class="dog-photo" role="img" aria-label="Photo of a tired red-brown dog lying down"></div>
  <p class="signs-label">SIGNS:</p>
  <ul class="signs-list">
    <li>increased breathing rate, excess panting</li>
    <li>reduced exercise ability, tiring quickly</li>
    <li>coughing or gagging</li>
    <li>restless sleeping</li>
  </ul>

  <p class="call-to-action">KEEP YOUR LOVED DOGS <strong>HEALTHY</strong><br>AND GET THEIR <span class="heart-word">HEART</span> <span class="checked-word">CHECKED</span> TODAY!</p>

  <svg class="heart-doodle" width="135" height="156" viewBox="0 0 135 156" aria-hidden="true">
    <path d="M48 120 C30 95 6 55 6 32 C6 12 22 6 35 14 C48 22 58 50 62 78 C68 45 85 8 106 8 C124 8 130 28 122 55 C108 95 78 128 50 148"
          fill="none" stroke="var(--red)" stroke-width="8" stroke-linecap="round" stroke-linejoin="round"/>
  </svg>
</main>
</body>
</html>
```